Brightmoor Lift Inc Website Deisgn

We are a new small elevator contracting company.
We would like a full website designed similar to
http://pellingtonlifts.com or https://www.northvalelifting.ca/
In addition to contents found on the above webpages.. we would like a section for project gallery etc.... have fun with it ... make it professional

Target Market(s)

Elevator Consultants - Property managers - Condo Boards - Commercial office buildings

Coding

Number of Pages Required

5+ page

Requirements
Must have
• Navigation Bar.. Be view able via mobile ..Should be pictures of Tall Office buildings in background.. Toronto city skyline etc....

Have Fun!

```html
<!DOCTYPE html>
<html lang="en">
<head>
<meta charset="UTF-8">
<title>Brightmoor Lift Inc</title>
<link href="https://fonts.googleapis.com/css2?family=Poppins:wght@400;500;600;700;800&display=swap" rel="stylesheet">
<style>
:root{
  --red:#c52d45;
  --navy:#1c1f3a;
  --ink:#222;
  --body:#444;
  --grey-bg:#ececec;
  --white:#fff;
  --line:#cfcfcf;
}
*{box-sizing:border-box;margin:0;padding:0}
html,body{width:1200px;height:4543px;overflow:hidden}
body{font-family:'Poppins',sans-serif;color:var(--ink);background:var(--white);position:relative}
section,header,footer{position:absolute;left:0;width:1200px}
.center{text-align:center}
.section-title{font-weight:800;font-size:42px;color:var(--ink);text-align:center;line-height:1}
.section-sub{font-size:13px;color:var(--body);text-align:center;line-height:21px;width:760px;margin:0 auto}

/* header */
.site-header{top:0;height:76px;background:var(--white);border-top:4px solid var(--navy)}
.brand{position:absolute;left:148px;top:20px;display:flex;align-items:center;gap:8px;font-weight:700;font-size:18px;color:var(--ink)}
.brand-dot{width:14px;height:14px;border-radius:50%;background:var(--ink)}
.main-nav{position:absolute;left:368px;top:28px;display:flex;gap:30px;font-size:13px;color:var(--body)}
.btn{display:inline-flex;align-items:center;justify-content:center;background:var(--red);color:var(--white);font-size:13px}
.nav-cta{position:absolute;left:915px;top:16px;width:134px;height:40px}

/* hero */
.hero{top:76px;height:594px;background:linear-gradient(180deg,#1a1712 0%,#2a2116 45%,#3a2a14 75%,#1b1610 100%)}
.hero-kicker{position:absolute;top:185px;width:100%;text-align:center;color:var(--white);font-size:24px;letter-spacing:1px}
.hero-title{position:absolute;top:228px;width:100%;text-align:center;color:var(--white);font-weight:800;font-size:48px;line-height:60px;letter-spacing:2px}
.hero-btn{position:absolute;left:533px;top:376px;width:134px;height:40px}

/* about */
.about{top:670px;height:318px;background:var(--grey-bg)}
.about .section-title{margin-top:80px}
.about-lead{margin:30px auto 0;width:900px;color:var(--red);font-size:13px;line-height:21px;text-align:center}
.about-text{margin:4px auto 0;width:900px;color:var(--body);font-size:13px;line-height:24px;text-align:center}

/* services */
.services{top:988px;height:679px}
.services .section-title{margin-top:76px}
.services .section-sub{margin-top:30px}
.service-card{position:absolute;top:225px;width:285px;height:371px;background:var(--white);box-shadow:0 0 10px rgba(0,0,0,.12);text-align:center}
.service-photo{display:block;margin:30px auto 0;width:245px;height:133px}
.service-card h3{margin-top:30px;font-weight:500;font-size:19px}
.service-card p{margin:20px 20px 0;font-size:13px;line-height:20px;color:var(--body)}
.service-link{display:block;margin-top:18px;font-size:12px;font-weight:500;color:var(--red)}

/* faq */
.faq{top:1667px;height:693px;background:var(--red);color:var(--white)}
.faq .section-title{color:var(--white);margin-top:76px}
.faq .section-sub{color:var(--white);margin-top:30px;width:740px}
.faq-item{position:absolute;left:186px;width:828px;border:1px solid rgba(255,255,255,.75);font-size:13px}
.faq-item.open{top:227px;height:143px;padding:22px 26px}
.faq-item.open h4{font-weight:500;font-size:16px}
.faq-item.open p{margin-top:14px;line-height:21px;width:740px}
.faq-item.closed{height:45px;padding:0 26px;display:flex;align-items:center}
.faq-toggle{position:absolute;right:22px;top:14px}
.faq-item.closed .faq-toggle{top:12px}

/* gallery */
.gallery{top:2360px;height:1164px}
.gallery .section-title{margin-top:82px}
.gallery .section-sub{margin-top:30px}
.tile{position:absolute;width:267px}

/* contact */
.contact{top:3524px;height:904px;background:var(--grey-bg)}
.contact .section-title{margin-top:80px}
.contact .section-sub{margin-top:30px;width:740px}
.info-card{position:absolute;top:225px;width:277px;height:161px;background:#f5f5f5;text-align:center;font-size:13px;line-height:22px;color:var(--ink)}
.info-card svg{display:block;margin:22px auto 24px}
.form-panel{position:absolute;left:150px;top:418px;width:432px;height:400px;background:#f5f5f5}
.field{position:absolute;left:47px;width:338px;height:32px;border:1px solid #9a9a9a;background:var(--white);font-size:11px;color:#777;padding:0 16px;display:flex;align-items:center}
.field.message{height:164px;align-items:flex-start;padding-top:12px}
.send-btn{position:absolute;left:343px;top:301px;width:42px;height:40px;background:var(--navy);display:flex;align-items:center;justify-content:center}
.map{position:absolute;left:616px;top:418px;width:433px;height:400px;background:linear-gradient(135deg,#e9ece8,#dfe4e6)}

/* footer */
.site-footer{top:4428px;height:115px;background:var(--navy);color:var(--white)}
.social{position:absolute;top:26px;left:0;width:100%;display:flex;justify-content:center;gap:16px}
.social span{width:27px;height:27px;border-radius:50%;background:#4a6fd8}
.legal{position:absolute;top:72px;width:100%;text-align:center;font-size:12px}
</style>
</head>
<body>

<header class="site-header">
  <div class="brand"><span class="brand-dot"></span>Brightmoor Lift Inc</div>
  <nav class="main-nav">
    <span>Home</span><span>Our Services</span><span>Employees</span><span>FAQs</span><span>Free Quote</span><span>Contact Us</span>
  </nav>
  <span class="btn nav-cta">Free Quote</span>
</header>

<section class="hero" role="img" aria-label="Night view of lit office towers in the Toronto skyline">
  <p class="hero-kicker">WE ARE TORONTO’S #1 CHOICE FOR</p>
  <h1 class="hero-title">Elevator Maintenance, Repair &amp;<br>Modernization</h1>
  <span class="btn hero-btn">Learn More</span>
</section>

<section class="about">
  <h2 class="section-title">About Brightmoor Lift</h2>
  <p class="about-lead">Lorem ipsum dolor sit amet, consectetur an adipiscing elit, sed do eiusmod tempor incididunt ut labore man et dolore magna<br>sed do eiusmod tempor incididunt ut &nbsp;aliqua.</p>
  <p class="about-text">Ut enim ad minim veniam, quis monda nostrud monda &nbsp;exercitation ullamco na malaboris nisi ut aliquip ex eab a acommodo<br>consequat. Duis aute irure dolor in manreprehenderit , in voluptate velit esse cillum dolore eu fugiat a nulla pariatur.</p>
</section>

<section class="services">
  <h2 class="section-title">Services We Offer</h2>
  <p class="section-sub">Lorem ipsum dolor sit amet, consectetur an adipiscing elit, sed do eiusmod tempor<br>incididunt ut labore man et dolore magna aliqua.</p>
  <article class="service-card" style="left:150px">
    <div class="service-photo" role="img" aria-label="Office tower lit at night" style="background:linear-gradient(135deg,#2a2520,#6b5a44 60%,#1e1a16)"></div>
    <h3>Modernization</h3>
    <p>Lorem ipsum dolor sit amet, consectetur adipiscing elit, sed do eiusmod tempor...</p>
    <span class="service-link">Free Quote</span>
  </article>
  <article class="service-card" style="left:457px">
    <div class="service-photo" role="img" aria-label="Technician working on a glass building facade" style="background:linear-gradient(135deg,#4f6f99,#9fb4cc 55%,#6a84a8)"></div>
    <h3>Maintenance</h3>
    <p>Lorem ipsum dolor sit amet, consectetur adipiscing elit, sed do eiusmod tempor...</p>
    <span class="service-link">Free Quote</span>
  </article>
  <article class="service-card" style="left:765px">
    <div class="service-photo" role="img" aria-label="Red wrench tool on dark surface" style="background:linear-gradient(135deg,#2b2b2e,#6e3038 55%,#1c1c1e)"></div>
    <h3>Other Services</h3>
    <p>Lorem ipsum dolor sit amet, consectetur adipiscing elit, sed do eiusmod tempor...</p>
    <span class="service-link">Free Quote</span>
  </article>
</section>

<section class="faq">
  <h2 class="section-title">Frequently Ask Questions</h2>
  <p class="section-sub">Lorem ipsum dolor sit amet, consectetur an adipiscing elit, sed do eiusmod tempor incididunt ut labore man et dolore magna aliqua.</p>
  <div class="faq-item open">
    <h4>Lorem ipsum dolor sit amet, consectetur?</h4>
    <p>Lorem ipsum dolor sit amet, consectetur adipiscing elit, sed do eiusmod tempor incididunt ut labore et dolore magna aliqua. Ut enim ad minim veniam, quis nostrud exercitation ullamco laboris nisi ut aliquip ex ea commodo consequat.</p>
    <svg class="faq-toggle" width="20" height="20" viewBox="0 0 20 20"><circle cx="10" cy="10" r="10" fill="#f08a4b"/><rect x="5" y="9" width="10" height="2" fill="#fff"/></svg>
  </div>
  <div class="faq-item closed" style="top:385px">Lorem ipsum dolor sit amet, consectetur?<svg class="faq-toggle" width="20" height="20" viewBox="0 0 20 20"><circle cx="10" cy="10" r="10" fill="#fff"/><rect x="5" y="9" width="10" height="2" fill="#c52d45"/><rect x="9" y="5" width="2" height="10" fill="#c52d45"/></svg></div>
  <div class="faq-item closed" style="top:445px">Lorem ipsum dolor sit amet, consectetur?<svg class="faq-toggle" width="20" height="20" viewBox="0 0 20 20"><circle cx="10" cy="10" r="10" fill="#fff"/><rect x="5" y="9" width="10" height="2" fill="#c52d45"/><rect x="9" y="5" width="2" height="10" fill="#c52d45"/></svg></div>
  <div class="faq-item closed" style="top:505px">Lorem ipsum dolor sit amet, consectetur?<svg class="faq-toggle" width="20" height="20" viewBox="0 0 20 20"><circle cx="10" cy="10" r="10" fill="#fff"/><rect x="5" y="9" width="10" height="2" fill="#c52d45"/><rect x="9" y="5" width="2" height="10" fill="#c52d45"/></svg></div>
  <div class="faq-item closed" style="top:565px">Lorem ipsum dolor sit amet, consectetur?<svg class="faq-toggle" width="20" height="20" viewBox="0 0 20 20"><circle cx="10" cy="10" r="10" fill="#fff"/><rect x="5" y="9" width="10" height="2" fill="#c52d45"/><rect x="9" y="5" width="2" height="10" fill="#c52d45"/></svg></div>
</section>

<section class="gallery">
  <h2 class="section-title">Our Project Gallery</h2>
  <p class="section-sub">Lorem ipsum dolor sit amet, consectetur an adipiscing elit, sed do eiusmod tempor<br>incididunt ut labore man et dolore magna aliqua.</p>
  <div class="tile" role="img" aria-label="Glass tower seen from below" style="left:184px;top:229px;height:184px;background:linear-gradient(135deg,#1f3550,#5f86ad 60%,#d9e2ea)"></div>
  <div class="tile" role="img" aria-label="Golden glass skyscraper against blue sky" style="left:184px;top:428px;height:341px;background:linear-gradient(135deg,#c8882e,#3a6fa8 55%,#8ec3ea)"></div>
  <div class="tile" role="img" aria-label="Aerial view of a dense city" style="left:184px;top:784px;height:185px;background:linear-gradient(135deg,#3d4446,#7a8078 60%,#2e3334)"></div>
  <div class="tile" role="img" aria-label="City towers at night with light trails" style="left:466px;top:229px;height:319px;background:linear-gradient(180deg,#08131f,#1d3c4f 60%,#9fb2b8)"></div>
  <div class="tile" role="img" aria-label="Black and white office towers" style="left:466px;top:562px;height:319px;background:linear-gradient(135deg,#d8d8d8,#2b2b2b 55%,#9a9a9a)"></div>
  <div class="tile" role="img" aria-label="Lit office windows at night" style="left:466px;top:896px;height:185px;background:linear-gradient(135deg,#1a1510,#5a4120 55%,#120f0c)"></div>
  <div class="tile" role="img" aria-label="Downtown towers at sunset" style="left:748px;top:229px;height:184px;background:linear-gradient(180deg,#2f7fb0,#b08a55 60%,#4a3524)"></div>
  <div class="tile" role="img" aria-label="Stacked parking levels with red lighting" style="left:748px;top:428px;height:319px;background:linear-gradient(180deg,#3a2f33,#7a2a34 50%,#2a2427)"></div>
  <div class="tile" role="img" aria-label="Toronto skyline at dusk" style="left:748px;top:762px;height:185px;background:linear-gradient(180deg,#10263f,#2d4f72 55%,#7a5a30)"></div>
</section>

<section class="contact">
  <h2 class="section-title">Contact Us</h2>
  <p class="section-sub">Lorem ipsum dolor sit amet, consectetur an adipiscing elit, sed do eiusmod tempor incididunt ut labore man et dolore magna aliqua.</p>
  <div class="info-card" style="left:150px">
    <svg width="24" height="28" viewBox="0 0 24 28"><path d="M12 2a9 9 0 0 0-9 9c0 7 9 15 9 15s9-8 9-15a9 9 0 0 0-9-9z" fill="none" stroke="#c52d45" stroke-width="2"/><circle cx="12" cy="11" r="3" fill="none" stroke="#c52d45" stroke-width="2"/></svg>
    2870 Harlow Ridge<br>Blvd Ashcombe GA 30112
  </div>
  <div class="info-card" style="left:461px">
    <svg width="28" height="28" viewBox="0 0 28 28"><circle cx="14" cy="14" r="12" fill="none" stroke="#c52d45" stroke-width="2"/><path d="M9 8c0 6 5 11 11 11l1-3-3-1-1 1c-2-1-4-3-5-5l1-1-1-3z" fill="#c52d45"/></svg>
    Telephone:<br>+00 (0) 00 123 00 56
  </div>
  <div class="info-card" style="left:772px">
    <svg width="30" height="28" viewBox="0 0 30 28"><rect x="2" y="6" width="26" height="18" fill="none" stroke="#c52d45" stroke-width="2"/><path d="M2 6l13 10L28 6" fill="none" stroke="#c52d45" stroke-width="2"/></svg>
    Email:<br>info@brightmoorlift.com
  </div>
  <form class="form-panel">
    <div class="field" style="top:48px">Name</div>
    <div class="field" style="top:92px">Email</div>
    <div class="field" style="top:136px">Problem/Issue</div>
    <div class="field message" style="top:180px">Message</div>
    <div class="send-btn"><svg width="18" height="18" viewBox="0 0 18 18"><path d="M2 9l14-7-4 14-3-5z" fill="none" stroke="#fff" stroke-width="1.4"/></svg></div>
  </form>
  <div class="map" role="img" aria-label="Street map showing the office location"></div>
</section>

<footer class="site-footer">
  <div class="social"><span></span><span></span><span></span><span></span></div>
  <p class="legal">©2020 all right reserved &nbsp;&nbsp; | &nbsp;&nbsp; privacy policy</p>
</footer>

</body>
</html>
```